Business Card Design - ChoiceCraft

Looking for creative, modern design, two sided for ChoiceCraft that is consistent with color and feel of website www.choicecraftpro.net.
Updates

Back of card will be used to promote products or have a quote revolving around decisions, change, leadership, innovation, creativity. Back should also have space to promote website, but optional to use the icon. Front of the card will need to use the icon and have standard place for name, job title, phone and email. We are not looking to put a mailing address or fax. Also want space to place a few words/phrase explaining what we do...such as individual growth and organizational development or tools, training, information...in addition, want the facebook icon small on the front somewhere as we are also on facebook.

Vector file uploaded of icon.

Target Market(s)

Professional coaching for individual growth and organizational development

Industry/Entity Type

Business

Requirements
Must have
• Icon...see attached.

```html
<!DOCTYPE html>
<html lang="en">
<head>
<meta charset="utf-8">
<title>ChoiceCraft Business Card</title>
<link rel="stylesheet" href="https://fonts.googleapis.com/css2?family=Arimo:wght@400;700&family=Russo+One&display=swap">
<style>
  :root {
    --stage: #c9cbce;
    --card-white: #ffffff;
    --navy: #23307f;
    --royal: #2f5db0;
    --sky: #1e9fe0;
    --sky-light: #4fb4e8;
    --back-top: #3aa6df;
    --back-bottom: #1677c3;
    --silver: #a9b0bb;
    --ink: #1a1a1a;
    --ink-soft: #333a44;
    --white: #ffffff;
  }
  * { box-sizing: border-box; margin: 0; padding: 0; }
  html, body { width: 1200px; height: 398px; overflow: hidden; }
  body {
    background: var(--stage);
    font-family: "Arimo", Arial, sans-serif;
    position: relative;
  }
  .card {
    position: absolute;
    border-radius: 14px;
    overflow: hidden;
    box-shadow: 0 3px 8px rgba(0,0,0,0.25);
  }
  .card--front {
    left: 50px; top: 47px; width: 525px; height: 300px;
    background: var(--card-white);
  }
  .card--back {
    left: 606px; top: 47px; width: 521px; height: 298px;
    background: radial-gradient(ellipse at 35% 40%, var(--back-top), var(--back-bottom) 85%);
  }
  .wave { position: absolute; left: 0; top: 0; width: 525px; height: 300px; }

  .brand-mark {
    position: absolute; left: 46px; top: 22px; width: 118px; height: 118px;
    display: flex; align-items: center; justify-content: center;
    border-radius: 50%;
    background: radial-gradient(circle at 40% 35%, #e7ecf3, #a8b6c8 70%, #6f86a8);
    border: 6px solid var(--sky);
  }
  .brand-mark__name {
    font-family: "Arimo", Arial, sans-serif; font-weight: 700;
    font-size: 15px; color: var(--navy);
  }
  .company {
    position: absolute; right: 18px; top: 28px; text-align: right;
  }
  .company__name {
    font-family: "Russo One", "Arimo", sans-serif;
    font-size: 22px; color: var(--ink); letter-spacing: 0.3px; line-height: 1;
  }
  .company__tagline {
    margin-top: 6px; font-size: 13.5px; line-height: 15px; color: var(--ink-soft);
  }
  .person {
    position: absolute; left: 45px; top: 189px;
    font-size: 17px; font-weight: 700; color: var(--ink);
  }
  .person__title { font-size: 13px; font-weight: 400; color: var(--ink-soft); }

  .contact {
    position: absolute; right: 18px; top: 209px; list-style: none;
    text-align: right; color: var(--white); font-size: 13.5px; line-height: 18px;
  }
  .contact li { display: flex; justify-content: flex-end; align-items: center; gap: 5px; }
  .contact svg { width: 10px; height: 10px; fill: var(--white); }
  .contact .social-square { width: 9px; height: 9px; background: var(--white); display: inline-block; }

  .quotes { position: absolute; left: 34px; top: 24px; list-style: none; }
  .quote { margin-bottom: 17px; color: var(--white); position: relative; padding-left: 17px; }
  .quote__text { font-size: 14px; line-height: 18px; }
  .quote__text::before {
    content: "\201C"; position: absolute; left: 0; top: -4px;
    font-size: 24px; font-family: Georgia, serif; font-weight: 700;
  }
  .quote__text::after {
    content: "\201D"; font-size: 24px; font-family: Georgia, serif; font-weight: 700;
    vertical-align: -10px; margin-left: 2px; line-height: 0;
  }
  .quote__author { font-size: 14px; font-weight: 700; line-height: 18px; }

  .back-mark {
    position: absolute; left: 362px; top: 168px; width: 92px; height: 92px;
    border-radius: 50%; border: 5px solid rgba(255,255,255,0.35);
    background: rgba(255,255,255,0.12);
    display: flex; align-items: center; justify-content: center;
  }
  .back-mark__name { font-weight: 700; font-size: 12px; color: rgba(255,255,255,0.6); }
</style>
</head>
<body>
  <section class="card card--front" aria-label="Card front">
    <svg class="wave" viewBox="0 0 525 300" aria-hidden="true">
      <defs>
        <linearGradient id="bandFill" x1="0" y1="0" x2="1" y2="0">
          <stop offset="0" stop-color="#5a8fd0"/>
          <stop offset="0.5" stop-color="#2f5db0"/>
          <stop offset="1" stop-color="#23307f"/>
        </linearGradient>
        <linearGradient id="silverLine" x1="0" y1="0" x2="1" y2="0">
          <stop offset="0" stop-color="#7c8594"/>
          <stop offset="0.5" stop-color="#d6dbe2"/>
          <stop offset="1" stop-color="#8e97a5"/>
        </linearGradient>
      </defs>
      <path d="M0 258 C120 300 230 200 525 168 L525 300 L0 300 Z" fill="url(#silverLine)"/>
      <path d="M0 268 C140 300 240 208 525 178 L525 300 L0 300 Z" fill="url(#bandFill)"/>
      <path d="M0 272 C140 300 240 230 380 220 C300 240 200 300 130 300 L0 300 Z" fill="#1e9fe0"/>
      <path d="M0 285 C120 300 200 262 330 250 C240 268 180 300 120 300 L0 300 Z" fill="#4fb4e8"/>
    </svg>

    <div class="brand-mark" role="img" aria-label="ChoiceCraft brand mark">
      <span class="brand-mark__name">ChoiceCraft</span>
    </div>

    <header class="company">
      <h1 class="company__name">ChoiceCraft</h1>
      <p class="company__tagline">Supporting individual growth<br>and&nbsp; organizational development.</p>
    </header>

    <p class="person">Your Name, <span class="person__title">Title</span></p>

    <ul class="contact">
      <li><svg viewBox="0 0 10 10"><path d="M2 0.5 L3.8 2.6 L2.8 3.6 C3.5 5 5 6.5 6.4 7.2 L7.4 6.2 L9.5 8 L8.2 9.5 C4.5 9 1 5.5 0.5 1.8 Z"/></svg>123-456-789</li>
      <li><svg viewBox="0 0 10 10"><path d="M0 2 H10 V8.5 H0 Z M0.8 2.6 L5 5.6 L9.2 2.6" stroke="#2f5db0" stroke-width="0.8"/></svg>info@choicecraftpro.net</li>
      <li><svg viewBox="0 0 10 10"><circle cx="5" cy="5" r="4.6"/><path d="M0.4 5 H9.6 M5 0.4 V9.6" stroke="#2f5db0" stroke-width="0.7"/></svg>www.choicecraftpro.net</li>
      <li><span class="social-square"></span>/choicecraftpro</li>
    </ul>
  </section>

  <section class="card card--back" aria-label="Card back">
    <ul class="quotes">
      <li class="quote"><p class="quote__text">Try not to become a man of success, but rather a man of value.</p><p class="quote__author">- Marten Alvery</p></li>
      <li class="quote"><p class="quote__text">The only constant is change.</p><p class="quote__author">- Thessalon</p></li>
      <li class="quote"><p class="quote__text">We are what we repeatedly do. Excellence is not an act, it is a habit.</p><p class="quote__author">- Orestides</p></li>
      <li class="quote"><p class="quote__text">Simplicity is the ultimate sophistication.</p><p class="quote__author">- Lorenzo Vallari</p></li>
      <li class="quote"><p class="quote__text">Life is not fair - get used to it.</p><p class="quote__author">- Walt Brennan</p></li>
    </ul>
    <div class="back-mark" role="img" aria-label="Faint ChoiceCraft brand mark">
      <span class="back-mark__name">ChoiceCraft</span>
    </div>
  </section>
</body>
</html>
```